SitePress Direct-Booking Website for Bend, Oregon Vacation Rental — $750 Budget
Project Overview

We are looking for a talented SitePress designer/developer to create a clean, professional and inviting direct-booking website for Birch Lantern Retreat, an established short-term vacation rental in Bend, Oregon.

The property is currently successfully listed on Staynest and Hoplo. Our Staynest property has approximately a 4.98-star rating with more than 200 reviews, is an Staynest Visitor Pick, and ranks among the Top 1% of eligible homes.

Project Budget: $750

We will select the designer based on the quality of the initial concept, understanding of the property, proposed booking solution and ability to deliver a completed and functioning SitePress website.

Existing Staynest Listing

Please use our current Staynest listing as the primary reference for photographs, property details, amenities and design inspiration:

https://www.staynest-example.net/rooms/48172036

Original high-resolution photographs and additional property information will be provided to the selected designer.

Design Direction

We want the website to feel:

Upscale but comfortable
Warm and welcoming
Clean and uncluttered
Pacific Northwest / Central Oregon
Professional rather than corporate
Highly visual with large property photographs
Easy to navigate
Excellent on phones, tablets and desktop computers

We welcome creativity and want designers to show us their vision for the property rather than simply copying our Staynest listing.

The website should immediately communicate that Birch Lantern Retreat is a highly rated vacation rental in an excellent Bend location.

Key Property Features
3 bedrooms
2 bathrooms
Sleeps up to 6 guests
Pet friendly
Approximately a 5-minute walk to Bend's Tannery Row Quarter
Near restaurants, shopping and Larkspur Fields Pavilion
Private fenced backyard
Covered outdoor area
Off-street driveway parking
Fireplace
Well-equipped kitchen
Staynest Prime Keeper
Staynest Visitor Pick
Top 1% of eligible Staynest homes
Approximately 4.98 stars with 200+ guest reviews

Our location, guest reviews, cleanliness, comfort, backyard, pet-friendly accommodations and walkability should be major selling points throughout the website.

Website Structure

We anticipate approximately 6–7 pages:

Home

Large hero photograph with a strong opening message and prominent BOOK DIRECT and CHECK AVAILABILITY buttons.

The home page should quickly communicate:

BIRCH LANTERN RETREAT — BEND, OREGON

3 Bedrooms | 2 Baths | Sleeps 6 | Pet Friendly | Walk to Tannery Row

Our exceptional guest rating and Staynest history should also be prominently featured.

The House

Bedrooms, bathrooms, kitchen, living areas, backyard and major amenities.

Photo Gallery

Large, attractive and fast-loading photographs with an easy-to-use mobile gallery.

Location / Explore Bend

Tannery Row Quarter, Larkspur Fields Pavilion, Deschutes River, restaurants, breweries, shopping, downtown Bend and nearby outdoor recreation.

Guest Reviews

Selected guest reviews and prominent presentation of our strong Staynest reputation.

Availability & Book Direct

A simple and professional direct-booking experience.

Contact / FAQ

Contact information plus common questions regarding pets, parking, check-in/check-out, cancellations and other policies.

IMPORTANT — Direct Booking & Credit Card Requirements

We want guests to be able to book directly through the website without having to contact us first.

The website should use a proven SitePress vacation-rental booking plugin or system rather than a custom-built reservation/payment system.

Guests should be able to:

Select arrival and departure dates
See available dates
Enter number of guests
See nightly charges
See cleaning fees
See applicable lodging taxes and other charges
See the complete reservation total before paying
Enter guest/contact information
Pay securely by credit or debit card
Receive an automatic reservation confirmation

Paywell is our preferred credit-card processor.

Credit-card information must be processed securely through Paywell or another established payment processor. Credit-card information should NOT be stored directly on our SitePress website.

Staynest & Hoplo Calendar Synchronization

This is very important.

The direct-booking calendar must synchronize with our existing Staynest and Hoplo calendars to reduce the possibility of double bookings.

For this single-property website, we prefer a simple solution using Staynest/Hoplo calendar or iCal synchronization rather than an expensive monthly channel-management service, if practical.

The designer should clearly identify the booking plugin/system they propose using.

IMPORTANT — Tell Us Your Proposed Booking Solution

As part of your submission, please tell us:

Which SitePress booking plugin/system you recommend.
Whether it synchronizes availability with Staynest and Hoplo.
Whether it integrates directly with Paywell.
The initial cost of the plugin/software.
Any annual or monthly fees.
Whether any additional paid software or services will be required.

We strongly prefer a solution with little or no ongoing monthly software expense.

We do not want to select a designer and later discover that the proposed booking system requires an expensive monthly subscription.

SitePress & Technical Requirements

The completed project should include:

Fully functioning SitePress website
Responsive desktop/tablet/mobile design
Fast-loading pages
Optimized photographs
SSL/HTTPS compatibility
Direct-booking functionality
Paywell payment integration
Staynest calendar synchronization
Hoplo calendar synchronization
Automatic booking confirmations
Cleaning fee and lodging-tax calculations
Contact form
Vizor Maps/location integration
Basic spam/security protection
Vizor Metrics capability
Basic SEO setup
Search-engine submission capability
Easy owner editing of text, rates and photographs
Search Engine Optimization

The website should be structured for Vizor and other search engines.

Important search themes include:

Bend Oregon vacation rental
Bend Oregon vacation home
Tannery Row Quarter vacation rental
Vacation rental near Tannery Row Bend
Bend Oregon pet-friendly vacation rental
Bend vacation rental near Larkspur Fields Pavilion
Bend Oregon direct booking vacation rental

We are not expecting an extensive ongoing SEO campaign for the $750 project. We do expect proper page titles, descriptions, headings, image optimization and a good technical foundation for future SEO.

Ownership

Upon completion and final payment:

We own the completed SitePress website.
We receive full SitePress administrator access.
We control the domain and hosting accounts.
We own all custom design files created for the project.
All necessary login credentials are provided to us.
The website can be moved to another SitePress hosting provider in the future.
There should be no proprietary dependency on the developer after completion.
What We Want From Contestants

Please review our Staynest listing before submitting your concept.

We are particularly interested in seeing an initial homepage concept showing how you would present:

Birch Lantern Retreat
The Bend / Tannery Row location
Our photography
Our exceptional guest reviews and ratings
The Book Direct message
The availability/booking call-to-action

We will provide feedback on the concepts we like and work with the selected designer to refine and complete the website.

Our Goal

Our objective is straightforward:

Create a beautiful, trustworthy and easy-to-use website that encourages guests to book Birch Lantern Retreat directly with us.

The website will complement—not replace—our existing Staynest and Hoplo listings.

We want repeat guests and new customers to have an easy way to find the property, check availability and book directly while receiving the same professional experience they expect from a major vacation-rental platform.

Target Market(s)

Consumers looking to to travel to Mexico for vacation. Family or couples

Industry/Entity Type

Short term vacation rental industry

Coding

Coded - Design and coding required

Number of Pages Required

5+ page

Requirements
Must have
• Capabilities to accept credit card payments and link to other rental property sites calendars such as HOPLO and Staynset
Nice to have
• Option for best plugins for property rental

```html
<!DOCTYPE html>
<html lang="en">
<head>
<meta charset="utf-8">
<title>Birch Lantern Retreat — Bend, Oregon</title>
<link href="https://fonts.googleapis.com/css2?family=Montserrat:wght@400;500;600;700;800&display=swap" rel="stylesheet">
<style>
:root{
  --red:#d8123c;
  --ink:#1b1b1b;
  --text:#555;
  --muted:#777;
  --pink:#fdf0f2;
  --line:#e3e3e3;
  --gold:#e6a817;
}
*{box-sizing:border-box;margin:0;padding:0}
html,body{width:1200px;height:5124px;overflow:hidden}
body{font-family:'Montserrat',sans-serif;color:var(--ink);background:#fff;position:relative}
.abs{position:absolute}
b.red,.hl{color:var(--red);font-weight:700}
.ph{display:block}
.btn{display:inline-flex;align-items:center;justify-content:center;border-radius:30px;font-weight:700;font-size:14px;text-transform:uppercase;letter-spacing:.2px}
.btn-red{background:var(--red);color:#fff}
.btn-line{border:2px solid var(--red);color:var(--ink);background:#fff}
.sec-title{font-weight:500;font-size:40px;text-align:center;color:var(--ink)}
.arrow{width:22px;height:22px;border:1.5px solid #999;border-radius:50%;display:flex;align-items:center;justify-content:center}
.arrow.l{border-color:var(--red)}
.stars{color:var(--gold);letter-spacing:1px}

/* nav */
.site-nav{top:0;left:0;width:1200px;height:78px;border-bottom:1px solid var(--line)}
.logo{left:104px;top:29px;font-weight:700;font-size:17px;color:var(--ink);white-space:nowrap}
.menu{left:390px;top:31px;display:flex;gap:33px;font-size:13px;font-weight:500}
.menu .active{color:var(--red);position:relative}
.menu .active:after{content:"";position:absolute;left:-6px;right:-6px;top:45px;height:4px;background:var(--red)}
.search{left:924px;top:28px}
.contact-btn{left:972px;top:19px;width:116px;height:42px}

/* hero */
.hero-copy{left:112px;top:112px;width:480px}
.eyebrow{font-size:12px;font-weight:700;letter-spacing:.2px}
.hero-title{font-size:40px;font-weight:500;line-height:56px;margin-top:26px}
.hero-lead{font-size:12px;color:var(--text);line-height:25px;margin-top:14px;width:440px}
.hero-ctas{display:flex;gap:12px;margin-top:16px}
.hero-ctas .btn{height:40px;font-size:14px}
.facts{font-size:12.5px;font-weight:600;color:#333;margin-top:22px;white-space:nowrap}
.rating-card{margin-top:18px;width:446px;height:78px;background:#fff;box-shadow:0 2px 10px rgba(0,0,0,.18);display:flex;align-items:center;padding:0 20px;gap:18px}
.brand{display:flex;align-items:center;gap:6px;color:var(--red);font-size:20px;font-weight:600}
.brand i{width:14px;height:14px;border-radius:50%;background:var(--red);display:block}
.score{font-size:38px;font-weight:700;line-height:1}
.score-sub{font-size:12px;color:var(--text);line-height:20px}
.hero-photo{left:600px;top:78px;width:600px;height:572px;background:linear-gradient(180deg,#5c8ed6 0%,#9ec3ea 30%,#6f7d6b 55%,#5b6b4a 75%,#8d8a80 100%)}

/* about */
.about-photo{left:112px;top:742px;width:448px;height:347px;border-radius:4px;background:linear-gradient(135deg,#d9d4cc,#b89a7a 55%,#8c7360)}
.about-copy{left:638px;top:736px;width:450px}
.about-copy h2{font-size:40px;font-weight:500}
.about-copy p{font-size:12px;color:var(--text);line-height:24px;margin-top:16px}
.amen{display:grid;grid-template-columns:220px 220px;row-gap:20px;margin-top:18px}
.amen div{display:flex;align-items:center;gap:16px;font-size:15px;color:#555;white-space:nowrap}
.amen .wide{grid-column:1 / span 2}
.ic{width:48px;height:48px;border:1.5px solid var(--red);border-radius:50%;display:flex;align-items:center;justify-content:center;flex:none}

/* rating band */
.fav-band{left:112px;top:1186px;width:976px;height:132px;border:2px solid var(--red);border-radius:4px;display:flex;align-items:center}
.fav-band .cell{height:92px;display:flex;align-items:center;justify-content:center}
.fav-band .div{border-left:2px dashed #bbb}
.fav-title{font-size:20px;font-weight:600;text-align:center;line-height:26px}
.fav-text{font-size:16px;line-height:26px;padding:0 32px}
.big-num{font-size:30px;font-weight:500;text-align:center}
.big-sub{font-size:18px;text-align:center}

/* rooms */
.rooms-title{top:1396px;left:0;width:1200px}
.rooms{left:112px;top:1480px;display:flex;gap:12px}
.room{width:317px;height:413px;background:#fff;box-shadow:0 1px 8px rgba(0,0,0,.15);padding:8px;text-align:center}
.room .ph{width:301px;height:255px}
.room h3{font-size:19px;font-weight:500;margin-top:20px}
.room p{font-size:12.5px;color:var(--text);line-height:18px;margin:18px 24px 0}
.room .dot{width:14px;height:14px;border-radius:50%;background:var(--red);margin:16px auto 0}

/* features */
.features-bg{left:0;top:1980px;width:675px;height:478px;background:var(--pink)}
.features{left:106px;top:2008px}
.features h2{font-size:40px;font-weight:500}
.feat-grid{display:grid;grid-template-columns:250px 290px;row-gap:13px;margin-top:22px}
.feat-grid.one{grid-template-columns:540px;margin-top:14px}
.feat{display:flex;align-items:center;gap:22px;font-size:13px;color:#555;white-space:nowrap}
.feat svg{flex:none}
.features-photo{left:675px;top:1983px;width:525px;height:475px;background:linear-gradient(160deg,#6f8f3c,#4a5c32 40%,#8b5a3a 65%,#9a9a94)}

/* gallery */
.gallery-title{top:2556px;left:0;width:1200px}
.g1{left:112px;top:2642px;width:116px;height:382px;background:linear-gradient(180deg,#e8e6e2,#b9b4ac)}
.g2{left:242px;top:2642px;width:722px;height:382px;background:linear-gradient(170deg,#ebe8e2,#cfc7bb 60%,#9f9990)}
.g3{left:972px;top:2642px;width:116px;height:382px;background:linear-gradient(180deg,#6d8fb3,#5e6a4e 60%,#8f7b6a)}
.g-label{left:242px;top:2856px;width:722px;text-align:center;font-size:28px;font-weight:600;color:var(--red)}

/* explore */
.explore-photo{left:0;top:3122px;width:557px;height:522px;background:linear-gradient(180deg,#9fb3c4,#4e6149 35%,#2f3f2c 70%,#56634d)}
.explore-bg{left:557px;top:3122px;width:643px;height:522px;background:var(--pink)}
.explore{left:636px;top:3150px;width:460px}
.explore h2{font-size:40px;font-weight:500}
.place{display:flex;gap:20px;margin-top:22px}
.place .ic{width:62px;height:62px}
.place h3{font-size:20px;font-weight:500;margin-top:2px}
.place p{font-size:12.5px;color:var(--text);line-height:20px;margin-top:6px}
.explore .btn{width:160px;height:42px;margin-top:26px}

/* reviews */
.reviews-title{top:3734px;left:0;width:1200px}
.reviews{left:112px;top:3826px;display:flex;gap:30px}
.review{width:306px;height:254px;background:#fff;box-shadow:0 1px 8px rgba(0,0,0,.15);padding:20px 24px}
.rv-head{display:flex;align-items:center;gap:16px;position:relative}
.avatar{width:70px;height:70px;border-radius:50%;background:linear-gradient(135deg,#e9c9a8,#a87656)}
.rv-name{font-size:14px;font-weight:700}
.rv-meta{display:flex;align-items:center;gap:4px;margin-top:6px;font-size:11px}
.rv-meta i{width:12px;height:12px;border-radius:50%;background:#999;display:block}
.quote{position:absolute;right:0;top:4px;font-size:44px;color:#c9c9c9;font-weight:800;line-height:1}
.review p{font-size:11.5px;color:#444;line-height:20px;margin-top:18px}
.more{display:inline-block;font-size:11.5px;color:var(--red);text-decoration:underline;margin-top:16px}

/* cta */
.cta-a{left:112px;top:4178px;width:302px;height:334px;background:linear-gradient(180deg,#4f8ad4,#8bb0c9 35%,#6a7d5a 65%,#8a8a7a)}
.cta-mid{left:422px;top:4178px;width:358px;height:334px;background:var(--pink);text-align:center;padding-top:46px}
.cta-mid h2{font-size:34px;font-weight:500;line-height:44px}
.cta-mid p{font-size:12.5px;color:var(--text);line-height:22px;margin:16px 30px 0}
.cta-mid .btn{width:210px;height:44px;margin-top:30px;font-size:13px}
.cta-b{left:786px;top:4178px;width:302px;height:334px;background:linear-gradient(180deg,#6f9a48,#4f5f3b 45%,#7d786e)}

/* help band */
.help{left:0;top:4594px;width:1200px;height:180px;background:var(--red);color:#fff}
.help h2{position:absolute;left:114px;top:34px;font-size:42px;font-weight:500}
.help p{position:absolute;left:114px;top:106px;font-size:13px;line-height:25px;width:460px}
.help .btn{position:absolute;left:936px;top:72px;width:152px;height:44px;background:#fff;color:var(--red)}

/* footer */
.f-logo{left:114px;top:4874px;font-size:26px;font-weight:700;white-space:nowrap}
.f-input{left:112px;top:4929px;width:356px;height:46px;border:1px solid #bbb;border-radius:30px;font-size:12px;color:#666;padding:15px 28px}
.f-btn{left:112px;top:4984px;width:150px;height:42px}
.f-col h4{font-size:19px;font-weight:500}
.links{left:590px;top:4862px}
.links ul{list-style:none;margin-top:18px}
.links li{font-size:13px;color:#444;line-height:24px}
.contact{left:808px;top:4862px}
.c-row{display:flex;align-items:center;gap:14px;font-size:14px;color:#333;margin-top:16px;white-space:nowrap}
.c-row .pin{width:30px;height:30px;border-radius:50%;background:var(--red);display:flex;align-items:center;justify-content:center;flex:none}
.follow{margin-top:20px}
.social{display:flex;gap:8px;margin-top:12px}
.social i{width:26px;height:26px;border-radius:50%;display:block}
.copy{left:112px;top:5084px;width:976px;border-top:1px solid #ccc;padding-top:16px;text-align:center;font-size:11px;color:#555}
</style>
</head>
<body>

<header class="abs site-nav">
  <div class="abs logo">BIRCH LANTERN RETREAT</div>
  <nav class="abs menu">
    <span class="active">Home</span><span>The House</span><span>Gallery</span><span>Explore Bend</span><span>Reviews</span><span>FAQ</span>
  </nav>
  <svg class="abs search" width="24" height="24" viewBox="0 0 24 24" fill="none" stroke="#555" stroke-width="1.6"><circle cx="10" cy="10" r="7"/><path d="M15 15l6 6"/></svg>
  <a class="abs btn btn-red contact-btn">Contact</a>
</header>

<section>
  <div class="abs hero-copy">
    <div class="eyebrow">BIRCH LANTERN RETREAT BEND, OREGON</div>
    <h1 class="hero-title">Your <b class="hl">Bend Getaway,</b> Steps from the Tannery Row</h1>
    <p class="hero-lead">A beautifully appointed 3-bedroom home for up to 6 guests, perfectly located for exploring Bend, the Deschutes River and the Tannery Row Quarter</p>
    <div class="hero-ctas">
      <a class="btn btn-red" style="width:140px">Book Direct</a>
      <a class="btn btn-line" style="width:206px">Check Availability</a>
    </div>
    <div class="facts">3 Bedrooms | 2 Baths | Sleeps 6 | Pet Friendly | Walk to Tannery Row</div>
    <div class="rating-card">
      <div class="brand"><i></i>Staynest</div>
      <div><div class="score">5.0</div><div class="stars" style="font-size:13px">★★★★★</div></div>
      <div class="score-sub" style="padding-left:14px">Exceptional Guest<br>Rating<br>205 Reviews</div>
    </div>
  </div>
  <div class="abs ph hero-photo" role="img" aria-label="Front view of the gray craftsman house with white porch, flower beds and blue sky"></div>
</section>

<section>
  <div class="abs ph about-photo" role="img" aria-label="Bright living room with wood stove fireplace, beige sofa and ottoman"></div>
  <div class="abs about-copy">
    <h2>About <b class="hl">Us</b></h2>
    <p>Walk to the Tannery Row Quarter, enjoy the river, concerts, great food and everything Bend has to offer. Then come home to relax in comfort and style.</p>
    <div class="amen">
      <div><span class="ic"><svg width="24" height="24" viewBox="0 0 24 24" fill="none" stroke="#d8123c" stroke-width="1.6"><path d="M3 18V8M3 14h18v4M21 18v-4M6 14v-3h5v3"/></svg></span>3 Bedrooms</div>
      <div><span class="ic"><svg width="24" height="24" viewBox="0 0 24 24" fill="none" stroke="#d8123c" stroke-width="1.6"><path d="M3 12h18v3a4 4 0 01-4 4H7a4 4 0 01-4-4zM6 12V5a2 2 0 014 0"/></svg></span>2 Baths</div>
      <div><span class="ic"><svg width="24" height="24" viewBox="0 0 24 24" fill="none" stroke="#d8123c" stroke-width="1.6"><path d="M19 14A8 8 0 1110 5a6 6 0 009 9z"/></svg></span>Sleep 6</div>
      <div><span class="ic"><svg width="24" height="24" viewBox="0 0 24 24" fill="none" stroke="#d8123c" stroke-width="1.6"><circle cx="6" cy="10" r="2"/><circle cx="10" cy="6" r="2"/><circle cx="14" cy="6" r="2"/><circle cx="18" cy="10" r="2"/><path d="M8 18c0-3 2-5 4-5s4 2 4 5z"/></svg></span>Pet friendly</div>
      <div class="wide"><span class="ic"><svg width="24" height="24" viewBox="0 0 24 24" fill="none" stroke="#d8123c" stroke-width="1.6"><circle cx="13" cy="4" r="2"/><path d="M12 8l-3 5 3 2v6M12 8l3 4 3 1M9 13l-3 7"/></svg></span>Walk to Tannery Row</div>
    </div>
  </div>
</section>

<section class="abs fav-band">
  <div class="cell" style="width:244px"><div class="fav-title">Guest<br>Favourite</div></div>
  <div class="cell div" style="width:372px"><div class="fav-text">One of the most loved homes on Staynest, according to guests</div></div>
  <div class="cell div" style="width:190px;flex-direction:column"><div class="big-num">4.98</div><div style="font-size:18px;letter-spacing:1px">★★★★★</div></div>
  <div class="cell div" style="width:166px;flex-direction:column"><div class="big-num">205</div><div class="big-sub">Reviews</div></div>
</section>

<section>
  <h2 class="abs sec-title rooms-title">A Home <b class="hl">Designed For Relaxing</b></h2>
  <div class="abs arrow l" style="left:42px;top:1680px"><svg width="8" height="8" viewBox="0 0 8 8" fill="none" stroke="#d8123c" stroke-width="1.5"><path d="M5 1L2 4l3 3"/></svg></div>
  <div class="abs arrow" style="left:1136px;top:1680px"><svg width="8" height="8" viewBox="0 0 8 8" fill="none" stroke="#999" stroke-width="1.5"><path d="M3 1l3 3-3 3"/></svg></div>
  <div class="abs rooms">
    <article class="room"><div class="ph" role="img" aria-label="Living room with leather ottoman, sofas and TV console" style="background:linear-gradient(160deg,#e3ddd4,#a89480 60%,#6b5a4a)"></div><h3>Living Room</h3><p>Comfortable gathering space with a cozy fireplace and smart TV</p><div class="dot"></div></article>
    <article class="room"><div class="ph" role="img" aria-label="Open kitchen with white cabinets and dining table" style="background:linear-gradient(160deg,#e6e4df,#b7b0a6 55%,#6e6258)"></div><h3>Kitchen &amp; Dining</h3><p>Fully equipped kitchen and dining area for home-cooked meals.</p><div class="dot"></div></article>
    <article class="room"><div class="ph" role="img" aria-label="Backyard patio with fire table and chairs among rocks" style="background:linear-gradient(160deg,#6d5a48,#3e3a30 55%,#8a7a66)"></div><h3>Backyard</h3><p>Private outdoor space with seating, grill and room to unwind.</p><div class="dot"></div></article>
  </div>
</section>

<section>
  <div class="abs features-bg"></div>
  <div class="abs features">
    <h2>Key <b class="hl">Features</b></h2>
    <div class="feat-grid">
      <div class="feat"><svg width="18" height="18" viewBox="0 0 18 18"><circle cx="9" cy="9" r="9" fill="#d8123c"/><path d="M5 9h7M9 6l3 3-3 3" fill="none" stroke="#fff" stroke-width="1.6"/></svg>3 bedrooms</div>
      <div class="feat"><svg width="18" height="18" viewBox="0 0 18 18"><circle cx="9" cy="9" r="9" fill="#d8123c"/><path d="M5 9h7M9 6l3 3-3 3" fill="none" stroke="#fff" stroke-width="1.6"/></svg>Off-street driveway parking</div>
      <div class="feat"><svg width="18" height="18" viewBox="0 0 18 18"><circle cx="9" cy="9" r="9" fill="#d8123c"/><path d="M5 9h7M9 6l3 3-3 3" fill="none" stroke="#fff" stroke-width="1.6"/></svg>2 bathrooms</div>
      <div class="feat"><svg width="18" height="18" viewBox="0 0 18 18"><circle cx="9" cy="9" r="9" fill="#d8123c"/><path d="M5 9h7M9 6l3 3-3 3" fill="none" stroke="#fff" stroke-width="1.6"/></svg>Fireplace</div>
      <div class="feat"><svg width="18" height="18" viewBox="0 0 18 18"><circle cx="9" cy="9" r="9" fill="#d8123c"/><path d="M5 9h7M9 6l3 3-3 3" fill="none" stroke="#fff" stroke-width="1.6"/></svg>Sleeps up to 6 guests</div>
      <div class="feat"><svg width="18" height="18" viewBox="0 0 18 18"><circle cx="9" cy="9" r="9" fill="#d8123c"/><path d="M5 9h7M9 6l3 3-3 3" fill="none" stroke="#fff" stroke-width="1.6"/></svg>Well-equipped kitchen</div>
      <div class="feat"><svg width="18" height="18" viewBox="0 0 18 18"><circle cx="9" cy="9" r="9" fill="#d8123c"/><path d="M5 9h7M9 6l3 3-3 3" fill="none" stroke="#fff" stroke-width="1.6"/></svg>Pet friendly</div>
      <div class="feat"><svg width="18" height="18" viewBox="0 0 18 18"><circle cx="9" cy="9" r="9" fill="#d8123c"/><path d="M5 9h7M9 6l3 3-3 3" fill="none" stroke="#fff" stroke-width="1.6"/></svg>Staynest Prime Keeper</div>
      <div class="feat"><svg width="18" height="18" viewBox="0 0 18 18"><circle cx="9" cy="9" r="9" fill="#d8123c"/><path d="M5 9h7M9 6l3 3-3 3" fill="none" stroke="#fff" stroke-width="1.6"/></svg>Private fenced backyard</div>
      <div class="feat"><svg width="18" height="18" viewBox="0 0 18 18"><circle cx="9" cy="9" r="9" fill="#d8123c"/><path d="M5 9h7M9 6l3 3-3 3" fill="none" stroke="#fff" stroke-width="1.6"/></svg>Staynest Visitor Pick</div>
      <div class="feat"><svg width="18" height="18" viewBox="0 0 18 18"><circle cx="9" cy="9" r="9" fill="#d8123c"/><path d="M5 9h7M9 6l3 3-3 3" fill="none" stroke="#fff" stroke-width="1.6"/></svg>Covered outdoor area</div>
      <div class="feat"><svg width="18" height="18" viewBox="0 0 18 18"><circle cx="9" cy="9" r="9" fill="#d8123c"/><path d="M5 9h7M9 6l3 3-3 3" fill="none" stroke="#fff" stroke-width="1.6"/></svg>Top 1% of eligible Staynest homes</div>
    </div>
    <div class="feat-grid one">
      <div class="feat"><svg width="18" height="18" viewBox="0 0 18 18"><circle cx="9" cy="9" r="9" fill="#d8123c"/><path d="M5 9h7M9 6l3 3-3 3" fill="none" stroke="#fff" stroke-width="1.6"/></svg>Approximately 4.98 stars with 200+ guest reviews</div>
      <div class="feat"><svg width="18" height="18" viewBox="0 0 18 18"><circle cx="9" cy="9" r="9" fill="#d8123c"/><path d="M5 9h7M9 6l3 3-3 3" fill="none" stroke="#fff" stroke-width="1.6"/></svg>Approximately a 5-minute walk to Bend's Tannery Row Quarter</div>
      <div class="feat"><svg width="18" height="18" viewBox="0 0 18 18"><circle cx="9" cy="9" r="9" fill="#d8123c"/><path d="M5 9h7M9 6l3 3-3 3" fill="none" stroke="#fff" stroke-width="1.6"/></svg>Near restaurants, shopping and Larkspur Fields Pavilion</div>
    </div>
  </div>
  <div class="abs ph features-photo" role="img" aria-label="Backyard water fountain among river rocks beside a wooden fence and tree"></div>
</section>

<section>
  <h2 class="abs sec-title gallery-title">Our <b class="hl">Gallery</b></h2>
  <div class="abs arrow l" style="left:42px;top:2832px"><svg width="8" height="8" viewBox="0 0 8 8" fill="none" stroke="#d8123c" stroke-width="1.5"><path d="M5 1L2 4l3 3"/></svg></div>
  <div class="abs arrow" style="left:1136px;top:2832px"><svg width="8" height="8" viewBox="0 0 8 8" fill="none" stroke="#999" stroke-width="1.5"><path d="M3 1l3 3-3 3"/></svg></div>
  <div class="abs ph g1" role="img" aria-label="Bathroom with white vanity and shelving"></div>
  <div class="abs ph g2" role="img" aria-label="Bedroom with white bedding and window blinds"></div>
  <div class="abs ph g3" role="img" aria-label="Backyard patio chairs under trees"></div>
  <div class="abs g-label">Bedroom</div>
</section>

<section>
  <div class="abs ph explore-photo" role="img" aria-label="Aerial view of Bend neighborhoods and pine forest with mountains on the horizon"></div>
  <div class="abs explore-bg"></div>
  <div class="abs explore">
    <h2>Explore <b class="hl">Bend</b></h2>
    <div class="place"><span class="ic"><svg width="28" height="28" viewBox="0 0 24 24" fill="none" stroke="#d8123c" stroke-width="1.5"><path d="M5 8h14l-1 13H6zM9 8V6a3 3 0 016 0v2"/></svg></span><div><h3>Tannery Row Quarter</h3><p>Walk to shopping, dining, theater and more</p></div></div>
    <div class="place"><span class="ic"><svg width="28" height="28" viewBox="0 0 24 24" fill="none" stroke="#d8123c" stroke-width="1.5"><circle cx="14" cy="8" r="5"/><path d="M10 12l-6 8M11 3l6 10"/></svg></span><div><h3>Larkspur Fields Pavilion</h3><p>Live concerts and events just minutes away</p></div></div>
    <div class="place"><span class="ic"><svg width="28" height="28" viewBox="0 0 24 24" fill="none" stroke="#d8123c" stroke-width="1.5"><path d="M3 9c3-2 5 2 9 0s6 2 9 0M3 14c3-2 5 2 9 0s6 2 9 0M3 19c3-2 5 2 9 0s6 2 9 0"/></svg></span><div><h3>Deschutes River</h3><p>Enjoy riverside trails, paddleboarding, fishing and beautiful scenery.</p></div></div>
    <div class="place"><span class="ic"><svg width="28" height="28" viewBox="0 0 24 24" fill="none" stroke="#d8123c" stroke-width="1.5"><path d="M3 21V9h5v12M8 21V4h8v17M16 21v-9h5v9M2 21h20"/></svg></span><div><h3>Downtown Bend</h3><p>Explore restaurants, breweries, boutiques and local culture</p></div></div>
    <a class="btn btn-red">Explore Bend</a>
  </div>
</section>

<section>
  <h2 class="abs sec-title reviews-title">Loved By <b class="hl">Our Guests</b></h2>
  <div class="abs arrow l" style="left:42px;top:3944px"><svg width="8" height="8" viewBox="0 0 8 8" fill="none" stroke="#d8123c" stroke-width="1.5"><path d="M5 1L2 4l3 3"/></svg></div>
  <div class="abs arrow" style="left:1136px;top:3944px"><svg width="8" height="8" viewBox="0 0 8 8" fill="none" stroke="#999" stroke-width="1.5"><path d="M3 1l3 3-3 3"/></svg></div>
  <div class="abs reviews">
    <article class="review"><div class="rv-head"><div class="avatar" role="img" aria-label="Guest avatar"></div><div><div class="rv-name">Maren</div><div class="rv-meta"><i></i><span class="stars">★★★★★</span></div></div><span class="quote">”</span></div><p>Very cute place central to Tannery Row district. The water fountain in the back was very peaceful and we enjoyed our stay. Thank you!</p><a class="more">Read More</a></article>
    <article class="review"><div class="rv-head"><div class="avatar" role="img" aria-label="Guest avatar" style="background:linear-gradient(135deg,#c9a88a,#6b4c3a)"></div><div><div class="rv-name">Delphine</div><div class="rv-meta"><i></i><span class="stars">★★★★★</span></div></div><span class="quote">”</span></div><p>Great house in Bend, charming and very clean. Quiet neighborhood—we enjoyed our stay here. Ample parking. Well equipped kitchen. Bathrooms had extra amenities that</p><a class="more">Read More</a></article>
    <article class="review"><div class="rv-head"><div class="avatar" role="img" aria-label="Guest avatar" style="background:linear-gradient(135deg,#a9c6e8,#e3c79a)"></div><div><div class="rv-name">Ingrid</div><div class="rv-meta"><i></i><span class="stars">★★★★★</span></div></div><span class="quote">”</span></div><p>This place is amazing and the personal touches were over the top! Rosalie was so kind and communicative. Great location, great house and we will definitely</p><a class="more">Read More</a></article>
  </div>
</section>

<section>
  <div class="abs ph cta-a" role="img" aria-label="The house front with porch and flowering shrubs"></div>
  <div class="abs cta-mid">
    <h2>Ready For <b class="hl">Your<br>Bend Adventure?</b></h2>
    <p>A highly rated home. A fantastic location. A comfortable place to come back to. Check your dates and see what's available.</p>
    <a class="btn btn-red">Check Availability</a>
  </div>
  <div class="abs ph cta-b" role="img" aria-label="Covered backyard patio with table and chairs under trees"></div>
</section>

<section class="abs help">
  <h2>We're <b style="font-weight:700">Here to Help</b></h2>
  <p>Planning your stay? Find answers to common questions about pets, parking, check-in, check-out, reservations and more.</p>
  <a class="btn">View FAQ's</a>
</section>

<footer>
  <div class="abs f-logo">BIRCH LANTERN RETREAT</div>
  <div class="abs f-input">Enter email address</div>
  <a class="abs btn btn-red f-btn">Book Now</a>
  <div class="abs f-col links">
    <h4>Quick Links</h4>
    <ul><li>Home</li><li>The House</li><li>Gallery</li><li>Explore Bend</li><li>Reviews</li><li>FAQ</li><li>Contact Us</li></ul>
  </div>
  <div class="abs f-col contact">
    <h4>Contact Info</h4>
    <div class="c-row"><span class="pin"><svg width="14" height="14" viewBox="0 0 24 24" fill="#fff"><path d="M12 2a7 7 0 00-7 7c0 5 7 13 7 13s7-8 7-13a7 7 0 00-7-7zm0 9.5A2.5 2.5 0 1112 6.5a2.5 2.5 0 010 5z"/></svg></span>Cedar Loop Lane,USA-5820317</div>
    <div class="c-row"><span class="pin"><svg width="14" height="14" viewBox="0 0 24 24" fill="none" stroke="#fff" stroke-width="2"><rect x="3" y="5" width="18" height="14" rx="2"/><path d="M3 7l9 6 9-6"/></svg></span>info@birchlanternretreat.com</div>
    <h4 class="follow">Follow Us</h4>
    <div class="social"><i style="background:var(--red)"></i><i style="background:#bbb"></i></div>
  </div>
  <div class="abs copy">Copyrights © 2026 Birch Lantern Retreat.All rights reserved</div>
</footer>

</body>
</html>
```